Business Card Design Project

Business Card design based on logo.
Updates

I need business card, letterhead, envelope, and if possible, Powerpoint slide template.

On front of business card: Just logo- and  my name and title:  Harriet Lindqvist, Principal

On reverse-logo and the rest of the contact info:

4871 Quarry Lane
Davis, CA 95618
650-318-2764
hl@brackenstudyworks.example

On letterhead-Just logo at top, at bottom  the rest-very small along the bottom

On PPT slide-just the logo.

I also want to try a few other colors-I like lime/dark grey (not black) but would like to try Sienna, maybe also indigo or bright blue-green.

I forgot to add-

On the business card-switch to vertical on reverse side and put:

Reverse side-switch to vertical and list:

Harriet Lindqvist
Principal
Bracken Study Works, LLC

650-318-2764

4871 Quarry Lane
Davis, CA 95618

Harriet Lindqvist
Principal

650-318-2764

4871 Quarry Lane
Davis, CA 95618

I have another project at the same time-for Stationery. Feel free to submit to that one also.

That one includes letterhead, envelope, PPT slide, folder cover sheet-HL

Industry/Entity Type

Business

Requirements
Must have
• Must use logo-preferably lime green version-with gray, not black or just 2-tone -logo on colored background.

```html
<!DOCTYPE html>
<html lang="en">
<head>
<meta charset="utf-8">
<title>Bracken Study – Business Cards</title>
<link rel="stylesheet" href="https://fonts.googleapis.com/css2?family=Source+Sans+3:wght@400;600&display=swap">
<style>
  :root {
    --lime: #9cb92f;
    --lime-bright: #a3c131;
    --graphite: #444447;
    --graphite-deep: #3a3a3d;
    --ink: #4a4a4c;
    --paper: #ffffff;
    --stage: #2a2a2b;
    --black: #111111;
  }
  * { margin: 0; padding: 0; box-sizing: border-box; }
  html, body {
    width: 1200px; height: 722px; overflow: hidden;
    background: var(--stage);
    font-family: "Source Sans 3", "Myriad Pro", Arial, sans-serif;
  }
  .sheet { position: relative; width: 1200px; height: 722px; }
  .card {
    position: absolute; border-radius: 14px; overflow: hidden;
  }
  .card--front { left: 58px; top: 47px; width: 526px; height: 300px; background: var(--paper); }
  .card--white { left: 612px; top: 47px; width: 525px; height: 300px; background: var(--paper); }
  .card--lime  { left: 62px; top: 376px; width: 524px; height: 298px; background: var(--lime); }
  .card--grey  { left: 612px; top: 376px; width: 525px; height: 298px; background: var(--graphite); }

  .brand {
    position: absolute; display: flex; align-items: center; gap: 10px;
    font-weight: 600; text-transform: uppercase; letter-spacing: 3px;
    white-space: nowrap;
  }
  .brand__square { width: 14px; height: 14px; background: var(--lime); flex: none; }
  .card--front .brand { left: 40px; top: 136px; font-size: 26px; color: var(--ink); }
  .card--white .brand { left: 0; right: 0; justify-content: center; top: 150px; font-size: 38px; color: var(--ink); }
  .card--lime .brand { left: 0; right: 0; justify-content: center; top: 170px; font-size: 38px; color: var(--black); }
  .card--lime .brand__square { background: var(--black); }
  .card--grey .brand { left: 0; right: 0; justify-content: center; top: 140px; font-size: 46px; color: var(--lime-bright); }
  .card--grey .brand__square { width: 18px; height: 18px; }

  .holder { position: absolute; left: 317px; top: 64px; }
  .holder__name { font-size: 17px; font-weight: 600; color: var(--lime); line-height: 22px; }
  .holder__title { font-size: 13px; color: #666; line-height: 18px; }
  .contacts { list-style: none; margin-top: 14px; }
  .contacts li { display: flex; align-items: center; gap: 5px; font-size: 13px; color: #333; height: 19px; }
  .contacts svg { width: 10px; height: 10px; flex: none; }

  .wave { position: absolute; left: 0; bottom: 0; width: 526px; height: 300px; }
  .address {
    position: absolute; left: 318px; top: 250px; font-size: 13px; line-height: 19px; color: var(--paper);
  }

  .site {
    position: absolute; left: 0; right: 0; text-align: center;
    font-size: 12.5px; letter-spacing: 2px;
  }
  .card--white .site { top: 220px; color: #333; }
  .card--white .site span { color: var(--lime); }
  .card--lime .site { top: 245px; color: var(--paper); }
  .card--grey .site { top: 245px; color: #e8e8e8; }
  .card--grey .site span { color: var(--lime-bright); }
</style>
</head>
<body>
<main class="sheet">

  <section class="card card--front">
    <svg class="wave" viewBox="0 0 526 300" aria-hidden="true">
      <path d="M0,218 C70,262 150,282 240,270 C340,256 430,214 526,196 L526,300 L0,300 Z" fill="var(--graphite)"/>
      <path d="M0,205 C60,250 140,276 230,268 C330,258 430,212 526,190" fill="none" stroke="var(--paper)" stroke-width="6"/>
      <path d="M0,200 C60,246 140,272 230,264 C330,254 430,208 526,186" fill="none" stroke="var(--lime)" stroke-width="5"/>
      <path d="M20,222 C80,262 150,280 230,274" fill="none" stroke="var(--paper)" stroke-width="1.5"/>
    </svg>
    <div class="brand"><span class="brand__square"></span>Bracken Study</div>
    <div class="holder">
      <p class="holder__name">YOUR NAME</p>
      <p class="holder__title">Title</p>
      <ul class="contacts">
        <li><svg viewBox="0 0 10 10"><circle cx="5" cy="5" r="4.5" fill="none" stroke="var(--lime)"/><path d="M3.3,2.8 L4.3,4.3 L3.9,4.8 Q4.6,6 5.6,6.3 L6.1,5.9 L7.3,6.8 L6.7,7.4 Q4,7 2.8,3.5 Z" fill="var(--lime)"/></svg>0987 654321</li>
        <li><svg viewBox="0 0 10 10"><rect x="3" y="1" width="4" height="8" rx="1" fill="var(--lime)"/></svg>0987 654321</li>
        <li><svg viewBox="0 0 10 10"><rect x="1" y="2.5" width="8" height="5.5" fill="var(--lime)"/><path d="M1,2.5 L5,5.5 L9,2.5" fill="none" stroke="var(--paper)" stroke-width="0.8"/></svg>info@brackenstudy.example</li>
        <li><svg viewBox="0 0 10 10"><circle cx="5" cy="5" r="4.3" fill="none" stroke="var(--lime)" stroke-width="1.2"/><ellipse cx="5" cy="5" rx="1.8" ry="4.3" fill="none" stroke="var(--lime)" stroke-width="0.8"/><line x1="0.7" y1="5" x2="9.3" y2="5" stroke="var(--lime)" stroke-width="0.8"/></svg>www.brackenstudy.example</li>
      </ul>
    </div>
    <p class="address">00 Floor Complex<br>Street City Name 000 111</p>
  </section>

  <section class="card card--white">
    <div class="brand"><span class="brand__square"></span>Bracken Study</div>
    <p class="site">www.<span>brackenstudy</span>.example</p>
  </section>

  <section class="card card--lime">
    <div class="brand"><span class="brand__square"></span>Bracken Study</div>
    <p class="site">www.brackenstudy.example</p>
  </section>

  <section class="card card--grey">
    <div class="brand"><span class="brand__square"></span>Bracken Study</div>
    <p class="site">www.<span>brackenstudy</span>.example</p>
  </section>

</main>
</body>
</html>
```